Roofing Contractor business card redesign

I want to redesign my business card with a fresh, eye catching concept

Target Market(s)

Residential Roofing Clients, potential employees, and subcontractors.

Industry/Entity Type

Business

Colors

Designer to choose colors to be used in the design.

Requirements
Nice to have
• I just want something that's more pleasing to the eye. You can use a combination of either / or of my logos.

```html
<!DOCTYPE html>
<html lang="en">
<head>
<meta charset="utf-8">
<title>Fair Hands Building Contractors – Business Card</title>
<link rel="stylesheet" href="https://fonts.googleapis.com/css2?family=Oswald:wght@400;500&family=Source+Sans+3:wght@400;600;700&display=swap">
<style>
  :root {
    --backdrop: #232323;
    --orange: #e8772a;
    --maroon: #44110f;
    --brand-brown: #4a1511;
    --card-white: #ffffff;
    --text-light: #f6ece6;
    --art-warm: rgba(190, 90, 40, 0.35);
    --art-cream: rgba(240, 200, 130, 0.35);
  }
  * { margin: 0; padding: 0; box-sizing: border-box; }
  html, body { width: 1200px; height: 900px; overflow: hidden; }
  body {
    background: var(--backdrop);
    position: relative;
    font-family: "Source Sans 3", "Myriad Pro", sans-serif;
  }
  .card {
    position: absolute;
    top: 306px;
    width: 439px;
    height: 271px;
    border-radius: 10px;
    overflow: hidden;
  }
  .card-front { left: 150px; background: var(--maroon); }
  .card-back { left: 609px; background: var(--card-white); }

  .front-band {
    position: absolute; left: 0; top: 0; width: 100%; height: 112px;
    background: var(--orange);
  }
  .front-art {
    position: absolute; right: 0; top: 0; width: 160px; height: 271px;
    background: radial-gradient(ellipse at 60% 40%, var(--art-warm), rgba(0,0,0,0) 70%);
  }
  .back-art {
    position: absolute; left: 0; top: 0; width: 170px; height: 271px;
    background: radial-gradient(ellipse at 35% 55%, var(--art-cream), rgba(255,255,255,0) 72%);
  }

  .brand { position: absolute; color: var(--brand-brown); font-family: "Source Sans 3", sans-serif; font-weight: 700; }
  .brand-name { letter-spacing: -0.3px; white-space: nowrap; }
  .brand-sub { white-space: nowrap; }

  .front-brand { left: 22px; top: 22px; }
  .front-brand .brand-name { font-size: 36px; line-height: 42px; }
  .front-brand .brand-sub { font-size: 17px; line-height: 22px; margin-top: 4px; }

  .back-brand { left: 0; right: 0; top: 88px; text-align: center; }
  .back-brand .brand-name { font-size: 46px; line-height: 54px; }
  .back-brand .brand-sub { font-size: 22px; line-height: 28px; margin-top: 6px; }

  .person { position: absolute; left: 20px; top: 128px; color: var(--text-light); }
  .person-name { font-family: "Oswald", sans-serif; font-size: 20px; font-weight: 400; line-height: 26px; }
  .person-role { font-size: 13px; line-height: 16px; }

  .contact-list { position: absolute; left: 20px; top: 204px; list-style: none; color: var(--text-light); font-size: 12.5px; line-height: 16px; }
  .contact-list li { display: flex; align-items: center; gap: 5px; }
  .contact-list svg { width: 10px; height: 10px; fill: var(--text-light); }

  .address { position: absolute; right: 24px; top: 219px; text-align: right; color: var(--text-light); font-size: 12.5px; line-height: 16px; font-style: normal; }

  .website {
    position: absolute; left: 0; right: 0; top: 226px; text-align: center;
    font-family: "Oswald", sans-serif; font-size: 13px; font-weight: 500; color: var(--brand-brown);
  }
</style>
</head>
<body>
  <section class="card card-front">
    <div class="front-band"></div>
    <div class="front-art" role="img" aria-label="Faint illustration of a contractor in a hard hat holding a hammer"></div>
    <div class="brand front-brand">
      <div class="brand-name">Fair Hands</div>
      <div class="brand-sub">Building Contractors, Inc.</div>
    </div>
    <div class="person">
      <div class="person-name">Sam Porter</div>
      <div class="person-role">Keller certified Roof Inspector</div>
      <div class="person-role">Licensed Property Adjuster</div>
    </div>
    <ul class="contact-list">
      <li><svg viewBox="0 0 10 10"><path d="M1 3 Q5 0 9 3 L8 4.5 L6.5 3.8 L6.5 3 Q5 2.6 3.5 3 L3.5 3.8 L2 4.5 Z M2.5 5 H7.5 L8.5 9 H1.5 Z"/></svg>(555) 210-4800</li>
      <li><svg viewBox="0 0 10 10"><path d="M3 0.5 H7 V9.5 H3 Z M3.8 1.5 V7.5 H6.2 V1.5 Z"/></svg>(555) 318-2290</li>
      <li><svg viewBox="0 0 10 10"><path d="M0.5 2 H9.5 V8 H0.5 Z M1.2 2.6 L5 5.5 L8.8 2.6 Z"/></svg>sam@fairhandsbuild.com</li>
    </ul>
    <address class="address">4180 Cedar Lane Suite 110<br>Riverton, TX 75000</address>
  </section>

  <section class="card card-back">
    <div class="back-art" role="img" aria-label="Faint illustration of a smiling worker holding a power drill"></div>
    <div class="brand back-brand">
      <div class="brand-name">Fair Hands</div>
      <div class="brand-sub">Building Contractors, Inc.</div>
    </div>
    <div class="website">www.FairHandsBuild.com</div>
  </section>
</body>
</html>
```